Company or website name
- dalewintham.com
- Links to the website
- Vita Forge
- Describe your company and organization and target audience
- Founded by celebrity personal trainer and media personality Dale Wintham, Vita Forge provides high quality on-site fitness and wellness classes, and personal trainers for businesses and residential gyms throughout New York City. Our target audience are residents of high end buildings in NYC, that expect excellence and luxury
- The design should have the following
- This is a 24"x36" Poster for a complimentary event at a high end building. I would like the poster to look high end, luxury and simple and chique. The words should be clear and easy to read. It would be great to have a final copy that we can send to the printer and one which we can edit for future events Here is the text: The Halcott Spires Gym Complimentary Fitness & Wellness Event Complimentary Yoga, Pilates & Interval Training Bootcamp Classes PLUS: 30 Minute Private Training Sessions *Kids Karate Classes Also Available Saturday May 18th, 25th & June 1st Time: 9:00am - 12:15pm Halcott Spires Gym Schedule: 9:00am - 9:30am Yoga 9:45am - 10:15am Interval Training Bootcamp 11:45am -12:15pm Pilates 9:00am - 12:00pm Private Training Sessions Special Introductory Rate on Future Packages During Promotion www.Vitaforge.tv Info@vitaforge.tv
- Other Facts

```html
<!DOCTYPE html>
<html lang="en">
<head>
<meta charset="utf-8">
<title>The Halcott Spires Gym – Complimentary Fitness &amp; Wellness</title>
<link rel="stylesheet" href="https://fonts.googleapis.com/css2?family=Oswald:wght@500;700&family=Roboto+Condensed:wght@400;700&display=swap">
<style>
  :root {
    --ink: #000000;
    --paper: #ffffff;
    --sky: #1b8fdc;
    --sky-deep: #1446a8;
    --olive: #6f8b22;
    --lime: #8fc12b;
    --photo-dark: #1a1410;
    --photo-warm: #a47a5e;
  }
  * { box-sizing: border-box; margin: 0; padding: 0; }
  html, body { width: 1200px; height: 960px; overflow: hidden; background: var(--paper); }
  .canvas { position: relative; width: 1200px; height: 960px; }
  .poster {
    position: absolute; left: 300px; top: 31px; width: 600px; height: 895px;
    background: var(--ink); overflow: hidden; color: var(--paper);
    font-family: "Oswald", "Arial Narrow", sans-serif;
  }
  .poster > * { position: absolute; z-index: 2; }
  .schedule-band { left: 0; right: 0; top: 464px; height: 231px; background: var(--olive); z-index: 0; }
  .athlete-photo {
    left: 6px; top: 132px; width: 226px; height: 715px; z-index: 1;
    background: radial-gradient(ellipse 50% 50% at 50% 45%, var(--photo-warm) 0%, #6e4c3a 40%, var(--photo-dark) 75%, rgba(0,0,0,0) 100%);
    opacity: 0.7;
  }
  .title {
    top: 24px; left: 0; right: 0; text-align: center;
    font-weight: 700; font-size: 41px; line-height: 1; letter-spacing: 0.2px;
  }
  .subtitle {
    top: 72px; left: 0; right: 0; text-align: center;
    font-weight: 700; font-size: 30px; line-height: 1; color: var(--sky);
  }
  .class-banner { left: 201px; top: 131px; width: 387px; height: 134px; }
  .class-banner svg { position: absolute; inset: 0; }
  .class-banner p {
    position: relative; padding: 16px 12px 0 36px; text-align: center;
    font-family: "Roboto Condensed", "Arial Narrow", sans-serif;
    font-weight: 700; font-size: 21px; line-height: 34px;
  }
  .offer {
    left: 234px; top: 281px; width: 362px;
    font-weight: 700; font-size: 51px; line-height: 65px; white-space: nowrap;
  }
  .schedule {
    right: 14px; top: 506px; text-align: right; width: 470px;
    font-family: "Roboto Condensed", "Arial Narrow", sans-serif; font-size: 17px; line-height: 23px;
  }
  .schedule h2 {
    font-family: "Oswald", "Arial Narrow", sans-serif; font-weight: 500;
    font-size: 26px; line-height: 34px; letter-spacing: 0.5px;
  }
  .schedule li { list-style: none; white-space: nowrap; }
  .schedule li::before { content: "•"; }
  .schedule .dates { white-space: nowrap; }
  .contact {
    left: 20px; top: 508px; transform-origin: 0 0; transform: rotate(-90deg);
    white-space: nowrap; color: var(--lime);
    font-family: "Roboto Condensed", "Arial Narrow", sans-serif; font-size: 16px;
  }
  .contact span + span { margin-left: 10px; }
  .brand { left: 340px; top: 800px; display: flex; align-items: center; gap: 14px; white-space: nowrap; }
  .brand-dot { width: 20px; height: 20px; border-radius: 50%; background: var(--paper); }
  .brand-name { font-weight: 500; font-size: 40px; line-height: 1; letter-spacing: 1px; text-transform: uppercase; }
</style>
</head>
<body>
<div class="canvas">
  <main class="poster">
    <div class="schedule-band"></div>
    <div class="athlete-photo" role="img" aria-label="Photo of a female athlete in black sportswear throwing a punch mid-stride"></div>

    <h1 class="title">THE HALCOTT SPIRES GYM</h1>
    <p class="subtitle">COMPLIMENTARY FITNESS &amp; WELLNESS</p>

    <div class="class-banner">
      <svg viewBox="0 0 387 134" width="387" height="134" preserveAspectRatio="none" aria-hidden="true">
        <defs>
          <linearGradient id="banner-fill" x1="0" y1="0" x2="1" y2="1">
            <stop offset="0" stop-color="var(--sky)"/>
            <stop offset="1" stop-color="var(--sky-deep)"/>
          </linearGradient>
        </defs>
        <polygon points="28,0 387,0 387,134 0,134" fill="url(#banner-fill)"/>
      </svg>
      <p>COMPLIMENTARY YOGA,<br>PILATES &amp; INTERVAL TRAINING<br>BOOTCAMP CLASSES</p>
    </div>

    <p class="offer">PLUS: 30 Minute<br>Private Training<br>Sessions</p>

    <section class="schedule">
      <h2>SCHEDULE:</h2>
      <ul>
        <li>Halcott Spires Gym 9:00am - 9:30am</li>
        <li>Yoga 9:45am - 10:15am</li>
        <li>Interval Training Bootcamp 11:45am -12:15pm</li>
        <li>Pilates 9:00am - 12:00pm</li>
        <li>Kids Karate Classes Also Available</li>
      </ul>
      <p class="dates">Saturday May 18th, 25th &amp; June 1st Time: 9:00am - 12:15pm</p>
    </section>

    <p class="contact"><span>www.Vitaforge.tv</span><span>Info@vitaforge.tv</span></p>

    <div class="brand">
      <span class="brand-dot"></span>
      <span class="brand-name">Vita Forge</span>
    </div>
  </main>
</div>
</body>
</html>
```